Road Construction Company needs business cards

We would like a new business card designed for our business.

We're a road construction company based in Qld, Australia.

Can the business card please have the following information on it.

Name: Warren Halbeck
Position: General Manager
Phone: 0472 915 348
Email: Warren.halbeck@tovrin.com.au
Address: 87 Marrow Ave, Pendlebay, QLD, 4023
Website: www.tovrin.com.au

Visually we'd like the card to be professional and simple.

Attached is our logo.

Our website is www.tovrin.com.au

Target Market(s)

Men aged 25-60

Contact Information for Business Card

As listed in project description

Font styles to use
Serif

Requirements
Must have
• Large logo on back of card

```html
<!DOCTYPE html>
<html lang="en">
<head>
<meta charset="utf-8">
<title>Tovrin Business Card</title>
<link rel="stylesheet" href="https://fonts.googleapis.com/css2?family=Open+Sans:wght@400;600;700;800&display=swap">
<style>
  :root {
    --backdrop: #e6e4e1;
    --card: #1e1f24;
    --card-raised: #24252b;
    --card-deep: #1a1b1f;
    --brand-blue: #2a7fd2;
    --brand-blue-deep: #1f5fb8;
    --icon-blue: #1e63c4;
    --text-light: #f4f5f7;
    --mark-faint: #2b2c32;
  }
  * { box-sizing: border-box; margin: 0; padding: 0; }
  html, body {
    width: 1200px; height: 780px; overflow: hidden;
    background: var(--backdrop);
    font-family: "Open Sans", Arial, sans-serif;
  }
  .canvas {
    position: relative; width: 1200px; height: 780px;
  }
  .card {
    position: absolute; top: 100px;
    width: 330px; height: 580px;
    border-radius: 28px;
    background: var(--card);
    overflow: hidden;
    box-shadow: 0 14px 30px rgba(0,0,0,.28);
  }
  .card-back { left: 230px; }
  .card-front { left: 640px; }

  /* back */
  .back-wordmark {
    position: absolute; left: 50%; top: 50%;
    transform: translate(-50%, -50%) rotate(-90deg);
    font-size: 112px; font-weight: 800; letter-spacing: 4px;
    color: var(--mark-faint);
    white-space: nowrap;
  }

  /* front */
  .front-layers { position: absolute; inset: 0; }
  .front-content { position: absolute; inset: 0; text-align: center; color: var(--text-light); }
  .brand {
    position: absolute; top: 62px; left: 0; right: 0;
    display: flex; justify-content: center; align-items: center; gap: 10px;
  }
  .brand-dot { width: 14px; height: 14px; background: var(--brand-blue); }
  .brand-name {
    font-size: 40px; font-weight: 800; letter-spacing: 3px; color: var(--brand-blue);
  }
  .person { position: absolute; top: 250px; left: 0; right: 0; }
  .person-name {
    font-size: 29px; font-weight: 700; letter-spacing: .5px; color: var(--brand-blue);
    text-transform: uppercase; line-height: 1.1;
  }
  .person-role { font-size: 15px; font-weight: 600; margin-top: 2px; }
  .contact-icons {
    position: absolute; top: 320px; left: 0; right: 0;
    display: flex; justify-content: center; gap: 8px;
  }
  .contact-icons svg { width: 24px; height: 24px; }
  .contact-lines {
    position: absolute; top: 356px; left: 0; right: 0;
    font-size: 13.5px; line-height: 22px;
  }
  .address { position: absolute; top: 478px; left: 0; right: 0; font-size: 14px; line-height: 20px; }
  .address svg { width: 26px; height: 26px; display: block; margin: 0 auto 8px; }
</style>
</head>
<body>
<main class="canvas">

  <section class="card card-back" aria-label="Card back">
    <div class="back-wordmark">TOVRIN</div>
  </section>

  <section class="card card-front" aria-label="Card front">
    <svg class="front-layers" viewBox="0 0 330 580" width="330" height="580" aria-hidden="true">
      <defs>
        <filter id="layer-shadow" x="-20%" y="-20%" width="140%" height="140%">
          <feDropShadow dx="0" dy="6" stdDeviation="6" flood-color="#000" flood-opacity=".45"/>
        </filter>
      </defs>
      <rect width="330" height="580" fill="var(--card-deep)"/>
      <path d="M0 0 H330 V300 Q300 450 0 470 Z" fill="var(--card)" filter="url(#layer-shadow)"/>
      <path d="M0 0 H330 V250 Q330 440 40 445 Q20 445 0 440 Z" fill="var(--card-raised)" filter="url(#layer-shadow)"/>
      <path d="M0 0 H330 V250 Q330 440 40 445 Q20 445 0 440 Z" fill="var(--card)" opacity=".55"/>
    </svg>

    <div class="front-content">
      <div class="brand">
        <span class="brand-dot"></span>
        <span class="brand-name">TOVRIN</span>
      </div>

      <div class="person">
        <div class="person-name">Warren Halbeck</div>
        <div class="person-role">General Manager</div>
      </div>

      <div class="contact-icons">
        <svg viewBox="0 0 24 24" aria-label="Phone">
          <circle cx="12" cy="12" r="12" fill="var(--icon-blue)"/>
          <path d="M8.6 6.5 L10.4 8.8 L9.4 10 Q10.5 12.6 13.5 14.2 L14.7 13.2 L17 15 L15.8 16.9 Q11.8 17.2 8.8 13.5 Q6.6 10.4 7.2 7.6 Z" fill="#fff"/>
        </svg>
        <svg viewBox="0 0 24 24" aria-label="Email">
          <circle cx="12" cy="12" r="12" fill="var(--icon-blue)"/>
          <rect x="6" y="8" width="12" height="9" rx="1" fill="#fff"/>
          <path d="M6.5 8.5 L12 13 L17.5 8.5" fill="none" stroke="var(--icon-blue)" stroke-width="1.3"/>
        </svg>
        <svg viewBox="0 0 24 24" aria-label="Website">
          <circle cx="12" cy="12" r="12" fill="var(--icon-blue)"/>
          <circle cx="12" cy="12" r="6" fill="none" stroke="#fff" stroke-width="1.4"/>
          <ellipse cx="12" cy="12" rx="2.6" ry="6" fill="none" stroke="#fff" stroke-width="1.2"/>
          <path d="M6 12 H18" stroke="#fff" stroke-width="1.2"/>
        </svg>
      </div>

      <div class="contact-lines">
        <div>0472 915 348</div>
        <div>www.tovrin.com.au</div>
        <div>Warren.halbeck@tovrin.com.au</div>
      </div>

      <div class="address">
        <svg viewBox="0 0 26 26" aria-label="Location">
          <circle cx="13" cy="13" r="13" fill="var(--icon-blue)"/>
          <path d="M13 6 a4.5 4.5 0 0 1 4.5 4.5 c0 3.2 -4.5 8 -4.5 8 s-4.5 -4.8 -4.5 -8 A4.5 4.5 0 0 1 13 6 Z" fill="#fff"/>
          <circle cx="13" cy="10.5" r="1.7" fill="var(--icon-blue)"/>
        </svg>
        <div>87 Marrow Ave,</div>
        <div>Pendlebay, QLD, 4023</div>
      </div>
    </div>
  </section>

</main>
</body>
</html>
```